Pinecrest Real Estate A5 Flyer

A5 Flyer for print distribution.

Front (include attached photo and branding):
Pinecrest are a new face in the Dunmore & Kelvinhurst real estate market. The Pinecrest team are both Dunmore ‘locals’ and are genuinely and sincerely committed to this community. They put people first and pursue exceptional outcomes for their clients. This is the founding vision of Pinecrest.

Values:
Outstanding Customer Service
Timely Communication
Integrity Always
People First
Exceptional Negotiation

If you’re thinking of selling, interested in a free market appraisal, or simply want to find out more about the Pinecrest team, please reach out to Trevor or Owen for a chat. We’d love to shout you a coffee at The Marigold Coffee + Kitchen.

Pinecrest Real Estate
E: hello@pinecrestrealestate-example.com.au
W: pinecrestrealestate-example.com.au

Back (half the page about Trevor, other half the page about Owen). Please include headshots (Owen is the younger one):

Owen Pritchard (Property Consultant):

Owen has an in-depth understanding of all things property & finance related. With a degree in property & finance, diploma in finance & mortgage broking, certificate IV in real estate practice, project management roles in residential property development, plus years of small business experience as co-founder/co-owner of The Marigold Coffee + Kitchen, his experience in managing competing demands and complex scenarios runs far and wide.

Owen also has experience in corporate negotiations which is proving to be a very beneficial skill set. Owen is deeply committed to people and pursuing exceptional outcomes for his clients. He has built a reputation as a man of his word who is genuine and sincere and willing to go above and beyond for his clients.

owen@pinecrestrealestate-example.com.au
0400 118 204

Trevor Bungey (Director / Licensee):

Trevor has worked in various roles inclusive of being a Real Estate Agent, Bank Manager, Financial Counsellor, Mortgage Broker, and previously a Commercial Pilot. He spent eight years in remote Western Australia, where he worked for an international mining company creating strategies to help support the well-being of employees. Trevor’s focus in life has always been to help people. To him, it is always about the relationship. Trevor gets enormous satisfaction from seeing individuals, families, and businesses thrive financially. He has become a skilled negotiator with extensive experience working for a number of corporations and private firms.
 
What differentiates Trevor is his compassion and commitment to people. He works hard to be an excellent communicator with the aim of achieving great results. He  has extensive sales experience with incredible ability to push the boundaries, think outside the box and meet or surpass expectations. This is why his clients keep coming back and continue to refer well into the future. 

trevor@pinecrestrealestate-example.com.au
0400 362 917

Target Market(s)

House Sellers / House Buyers

Industry/Entity Type

Real Estate

Colors
0054AA
0677BA
7BADD7
CADEEF
E8F1F8

Requirements
Must have
• Branding / logo, river photo, head shots, company details etc
Nice to have
• Design as per attached branding guide

```html
<!DOCTYPE html>
<html lang="en">
<head>
<meta charset="utf-8">
<title>Pinecrest Real Estate – A5 Flyer</title>
<link rel="stylesheet" href="https://fonts.googleapis.com/css2?family=Cormorant+Garamond:wght@600;700&family=Roboto:wght@300;400;500&display=swap">
<style>
:root{
  --navy:#13222f;
  --grey:#6a6a6a;
  --text:#4a4a4a;
  --paper:#ffffff;
  --bg:#eeeeee;
  --line:#b9b9b9;
  --serif:"Cormorant Garamond", Georgia, serif;
  --sans:"Roboto", Arial, sans-serif;
}
*{box-sizing:border-box;margin:0;padding:0}
html,body{width:1200px;height:3712px;overflow:hidden}
body{background:var(--bg);font-family:var(--sans);color:var(--text);position:relative}
.page{position:absolute;left:147px;width:906px;height:1286px;background:var(--paper);box-shadow:0 2px 10px rgba(0,0,0,.12);overflow:hidden}
.page--front{top:962px}
.page--back{top:2340px}
.abs{position:absolute}

.brand{position:absolute;left:212px;top:42px;height:78px;display:flex;align-items:center;gap:30px}
.brand__dot{width:78px;height:78px;border-radius:50%;background:var(--navy)}
.brand__name{font-family:var(--serif);font-weight:600;font-size:46px;letter-spacing:12px;color:var(--navy)}

.hero-photo{left:46px;top:130px;width:812px;height:398px;background:linear-gradient(180deg,#c9d6e2 0%,#8aa6c0 22%,#3d6a93 45%,#2f5a45 70%,#6e7a6a 100%)}
.hero-banner{left:46px;top:528px;width:812px;height:190px;background:var(--navy);border-bottom-right-radius:62px;color:#fff;text-align:center;font-family:var(--serif);font-weight:700;text-transform:uppercase}
.hero-banner__top{font-size:37px;margin-top:16px;line-height:40px}
.hero-banner__main{font-size:60px;line-height:62px;letter-spacing:1px}
.hero-banner__bottom{font-size:37px;line-height:40px}

.intro,.closing{left:60px;width:786px;text-align:center;font-weight:300;font-size:17.5px;line-height:21px}
.intro{top:748px}
.closing{top:1108px}
.values-title{left:0;width:906px;top:837px;text-align:center;font-size:31px;font-weight:500;color:var(--navy)}
.values{left:52px;top:901px;display:flex;gap:7px}
.value{width:154px;height:162px;border:2px solid var(--navy);border-radius:10px;overflow:hidden;display:flex;flex-direction:column}
.value--alt{border-color:var(--grey)}
.value__icon{height:86px;display:flex;align-items:center;justify-content:center;background:#fff}
.value__label{flex:1;background:var(--navy);color:#fff;font-size:17px;line-height:17px;text-align:center;display:flex;align-items:center;justify-content:center;padding:0 4px}
.value--alt .value__label{background:var(--grey)}

.footer{left:0;bottom:0;width:906px;height:76px}
.footer svg{position:absolute;left:0;top:0}
.footer__item{position:absolute;top:0;height:76px;display:flex;align-items:center;gap:18px;color:#fff;font-size:20px}
.footer__item--email{left:52px}
.footer__item--web{left:524px;top:4px}

.agent-name{font-family:var(--serif);font-weight:700;font-size:50px;color:var(--navy);line-height:50px;text-transform:uppercase}
.agent-role{font-size:21px;font-weight:500;letter-spacing:4.5px;color:var(--navy);text-transform:uppercase;margin-top:6px}
.bio{font-weight:300;font-size:14.6px;line-height:18px;color:var(--text)}
.bio p+p{margin-top:18px}
.headshot{background:linear-gradient(180deg,#e9eaeb 0%,#d8dadc 55%,#2d3c57 56%,#25334c 100%);border:4px solid #fff}
.phone-bar{background:var(--grey);color:#fff;display:flex;align-items:center;gap:20px;font-family:var(--serif);font-weight:700;font-size:52px}
.agent-email{display:flex;align-items:center;gap:16px;font-size:19px;color:var(--navy)}
</style>
</head>
<body>

<!-- FRONT -->
<section class="page page--front">
  <div class="brand"><span class="brand__dot"></span><span class="brand__name">PINECREST</span></div>

  <div class="abs hero-photo" role="img" aria-label="Aerial photograph of the river foreshore and suburbs with the city skyline beyond"></div>
  <div class="abs hero-banner">
    <div class="hero-banner__top">Pinecrest are a new face in the</div>
    <div class="hero-banner__main">Dunmore &amp; Kelvinhurst</div>
    <div class="hero-banner__bottom">Real Estate Market</div>
  </div>

  <p class="abs intro">The Pinecrest team are both Dunmore ‘locals’ and are genuinely and sincerely committed to this community. They put people first and pursue exceptional outcomes for their clients. This is the founding vision of Pinecrest.</p>

  <h2 class="abs values-title">VALUES</h2>
  <div class="abs values">
    <div class="value">
      <div class="value__icon"><svg width="54" height="58" viewBox="0 0 54 58" fill="#13222f"><circle cx="27" cy="20" r="13"/><path d="M12 22a15 15 0 0 1 30 0" fill="none" stroke="#13222f" stroke-width="4"/><rect x="8" y="18" width="7" height="12" rx="3"/><rect x="39" y="18" width="7" height="12" rx="3"/><path d="M5 58c0-14 10-22 22-22s22 8 22 22z"/></svg></div>
      <div class="value__label">Outstanding<br>Customer<br>Service</div>
    </div>
    <div class="value value--alt">
      <div class="value__icon"><svg width="56" height="58" viewBox="0 0 56 58" fill="#13222f"><rect x="14" y="0" width="28" height="18" rx="5"/><circle cx="21" cy="9" r="2" fill="#fff"/><circle cx="28" cy="9" r="2" fill="#fff"/><circle cx="35" cy="9" r="2" fill="#fff"/><circle cx="14" cy="30" r="7"/><circle cx="42" cy="30" r="7"/><path d="M0 58c0-12 6-18 14-18s14 6 14 18z"/><path d="M28 58c0-12 6-18 14-18s14 6 14 18z"/></svg></div>
      <div class="value__label">Timely<br>Communication</div>
    </div>
    <div class="value">
      <div class="value__icon"><svg width="58" height="58" viewBox="0 0 58 58" fill="#13222f"><path d="M4 6h20v6a5 5 0 1 0 10 0V6h18v20h-6a5 5 0 1 0 0 10h6v18H34v-6a5 5 0 1 0-10 0v6H4V36h6a5 5 0 1 0 0-10H4z"/><path d="M29 6v48M4 31h48" stroke="#fff" stroke-width="2.5"/></svg></div>
      <div class="value__label">Integrity<br>Always</div>
    </div>
    <div class="value value--alt">
      <div class="value__icon"><svg width="58" height="58" viewBox="0 0 58 58" fill="#13222f"><circle cx="20" cy="9" r="8"/><path d="M14 20h12l10 18H24l-6 16H8l6-18z"/><ellipse cx="44" cy="50" rx="13" ry="7"/></svg></div>
      <div class="value__label">People<br>First</div>
    </div>
    <div class="value">
      <div class="value__icon"><svg width="60" height="58" viewBox="0 0 60 58" fill="#13222f"><circle cx="30" cy="12" r="11"/><path d="M24 12l4 4 8-8" fill="none" stroke="#fff" stroke-width="3"/><path d="M0 30l12-4 10 8 8-4 8 4 10-8 12 4v6l-12 4-16 14-12-8L0 38z"/></svg></div>
      <div class="value__label">Exceptional<br>Negotiation</div>
    </div>
  </div>

  <p class="abs closing">If you’re thinking of selling, interested in a free market appraisal, or simply want to find out more about the Pinecrest team, please reach out to Trevor or Owen for a chat.<br>We’d love to shout you a coffee at The Marigold Coffee + Kitchen.</p>

  <footer class="abs footer">
    <svg width="906" height="76" viewBox="0 0 906 76"><rect x="0" y="6" width="906" height="70" fill="#6a6a6a"/><path d="M0 0H448Q470 0 478 22L496 76H0Z" fill="#13222f" stroke="#fff" stroke-width="8"/><path d="M0 0H448Q470 0 478 22L496 76H0Z" fill="#13222f"/></svg>
    <div class="footer__item footer__item--email"><svg width="24" height="22" viewBox="0 0 24 22" fill="none" stroke="#fff" stroke-width="2"><rect x="1" y="6" width="22" height="15"/><path d="M1 6l11 8 11-8M5 6V1h14v5"/></svg>hello@pinecrestrealestate-example.com.au</div>
    <div class="footer__item footer__item--web"><svg width="24" height="24" viewBox="0 0 24 24" fill="none" stroke="#fff" stroke-width="2"><circle cx="12" cy="12" r="10"/><ellipse cx="12" cy="12" rx="4.5" ry="10"/><path d="M2 12h20M4 6h16M4 18h16"/></svg>pinecrestrealestate-example.com.au</div>
  </footer>
</section>

<!-- BACK -->
<section class="page page--back">
  <div class="brand"><span class="brand__dot"></span><span class="brand__name">PINECREST</span></div>

  <!-- Owen -->
  <div class="abs" style="left:0;top:195px;width:44px;height:368px;background:var(--navy)"></div>
  <div class="abs headshot" role="img" aria-label="Headshot of Owen Pritchard" style="left:40px;top:181px;width:337px;height:421px;border-radius:0 60px 60px 10px"></div>
  <div class="abs" style="left:402px;top:130px">
    <div class="agent-name">Owen Pritchard</div>
    <div class="agent-role">Property Consultant</div>
  </div>
  <div class="abs bio" style="left:403px;top:229px;width:450px">
    <p>Owen has an in-depth understanding of all things property &amp; finance related. With a degree in property &amp; finance, diploma in finance &amp; mortgage broking, certificate IV in real estate practice, project management roles in residential property development, plus years of small business experience as co-founder/co-owner of The Marigold Coffee + Kitchen, his experience in managing competing demands and complex scenarios runs far and wide.</p>
    <p>Owen also has experience in corporate negotiations which is proving to be a very beneficial skill set. Owen is deeply committed to people and pursuing exceptional outcomes for his clients. He has built a reputation as a man of his word who is genuine and sincere and willing to go above and beyond for his clients.</p>
  </div>
  <div class="abs phone-bar" style="left:377px;top:491px;width:473px;height:71px;padding-left:38px;border-top-left-radius:26px">
    <svg width="22" height="22" viewBox="0 0 24 24" fill="#fff"><path d="M6 2l4 5-2 3a12 12 0 0 0 6 6l3-2 5 4-3 4C10 22 2 14 2 5z"/></svg>0400 118 204
  </div>
  <div class="abs agent-email" style="left:410px;top:572px"><svg width="24" height="22" viewBox="0 0 24 22" fill="none" stroke="#13222f" stroke-width="2"><rect x="1" y="6" width="22" height="15"/><path d="M1 6l11 8 11-8M5 6V1h14v5"/></svg>owen@pinecrestrealestate-example.com.au</div>

  <div class="abs" style="left:55px;top:635px;width:790px;border-top:2px dotted var(--line)"></div>

  <!-- Trevor -->
  <div class="abs" style="left:55px;top:660px">
    <div class="agent-name">Trevor Bungey</div>
    <div class="agent-role">Director / Licensee</div>
  </div>
  <div class="abs bio" style="left:55px;top:755px;width:452px;line-height:16.6px">
    <p>Trevor has worked in various roles inclusive of being a Real Estate Agent, Bank Manager, Financial Counsellor, Mortgage Broker, and previously a Commercial Pilot. He spent eight years in remote Western Australia, where he worked for an international mining company creating strategies to help support the well-being of employees. Trevor’s focus in life has always been to help people. To him, it is always about the relationship. Trevor gets enormous satisfaction from seeing individuals, families, and businesses thrive financially. He has become a skilled negotiator with extensive experience working for a number of corporations and private firms.</p>
    <p style="margin-top:16px">What differentiates Trevor is his compassion and commitment to people. He works hard to be an excellent communicator with the aim of achieving great results. He has extensive sales experience with incredible ability to push the boundaries, think outside the box and meet or surpass expectations. This is why his clients keep coming back and continue to refer well into the future.</p>
  </div>
  <div class="abs" style="left:845px;top:748px;width:61px;height:379px;background:var(--navy)"></div>
  <div class="abs headshot" role="img" aria-label="Headshot of Trevor Bungey" style="left:514px;top:697px;width:336px;height:487px;border-radius:60px 0 10px 60px"></div>
  <div class="abs phone-bar" style="left:50px;top:1082px;width:474px;height:70px;padding-left:20px;border-top-right-radius:26px">
    <svg width="22" height="22" viewBox="0 0 24 24" fill="#fff"><path d="M6 2l4 5-2 3a12 12 0 0 0 6 6l3-2 5 4-3 4C10 22 2 14 2 5z"/></svg>0400 362 917
  </div>
  <div class="abs agent-email" style="left:66px;top:1166px"><svg width="24" height="22" viewBox="0 0 24 22" fill="none" stroke="#13222f" stroke-width="2"><rect x="1" y="6" width="22" height="15"/><path d="M1 6l11 8 11-8M5 6V1h14v5"/></svg>trevor@pinecrestrealestate-example.com.au</div>

  <footer class="abs footer">
    <svg width="906" height="76" viewBox="0 0 906 76"><rect x="0" y="6" width="906" height="70" fill="#6a6a6a"/><path d="M0 0H448Q470 0 478 22L496 76H0Z" fill="#13222f" stroke="#fff" stroke-width="8"/><path d="M0 0H448Q470 0 478 22L496 76H0Z" fill="#13222f"/></svg>
    <div class="footer__item footer__item--email"><svg width="24" height="22" viewBox="0 0 24 22" fill="none" stroke="#fff" stroke-width="2"><rect x="1" y="6" width="22" height="15"/><path d="M1 6l11 8 11-8M5 6V1h14v5"/></svg>hello@pinecrestrealestate-example.com.au</div>
    <div class="footer__item footer__item--web"><svg width="24" height="24" viewBox="0 0 24 24" fill="none" stroke="#fff" stroke-width="2"><circle cx="12" cy="12" r="10"/><ellipse cx="12" cy="12" rx="4.5" ry="10"/><path d="M2 12h20M4 6h16M4 18h16"/></svg>pinecrestrealestate-example.com.au</div>
  </footer>
</section>

</body>
</html>
```